Business Card Design For A Renovation Contractor Company

We need a business card for a new company based in Singapore, our company name is "RB Tolvane". We are a renovation contractor that builds designs into reality. We build more of F&B restaurants, retail stores and commercial offices. We work very closely with designers. The final design should communicate to our client that we are a company that you can trust, that will plan and complete your project without giving you a headache. I like my client to remember my company as "RB". The beauty of SIMPLE is important.

Industry/Entity Type

Contractor

Requirements
Nice to have
• Black or Red base

```html
<!DOCTYPE html>
<html lang="en">
<head>
<meta charset="utf-8">
<title>RB Tolvane — Business Card</title>
<link rel="stylesheet" href="https://fonts.googleapis.com/css2?family=Arimo:wght@400;700&family=Questrial&display=swap">
<style>
  :root {
    --brand-red: #e8202a;
    --brand-red-deep: #c8141d;
    --ink: #1b1b1b;
    --ink-soft: #4a4a4a;
    --paper: #ffffff;
    --stage: #ecebe8;
    --card-w: 525px;
    --card-h: 300px;
  }
  * { box-sizing: border-box; margin: 0; padding: 0; }
  html, body {
    width: 1200px; height: 720px; overflow: hidden;
    background: var(--stage);
  }
  .canvas {
    position: relative; width: 1200px; height: 720px;
    display: flex; align-items: center; justify-content: center; gap: 50px;
  }
  .card {
    position: relative; width: var(--card-w); height: var(--card-h);
    overflow: hidden; border-radius: 3px;
    box-shadow: 0 6px 18px rgba(0,0,0,.14);
  }

  /* Front */
  .card-front { background: var(--brand-red); }
  .front-head {
    position: absolute; left: 0; top: 0; width: 100%; height: 132px;
    background: var(--paper);
    display: flex; flex-direction: column; align-items: center; justify-content: center;
  }
  .wordmark {
    display: flex; align-items: center; gap: 10px;
    font-family: "Questrial", sans-serif; font-size: 40px; color: var(--ink);
    letter-spacing: -0.5px; line-height: 1;
  }
  .wordmark-dot {
    width: 30px; height: 30px; border-radius: 50%; background: var(--brand-red);
  }
  .tagline {
    margin-top: 6px; padding-top: 3px;
    border-top: 1.5px solid var(--ink);
    font-family: "Arimo", sans-serif; font-size: 14px; color: var(--brand-red);
    letter-spacing: 0.6px;
  }
  .front-mark {
    position: absolute; right: 40px; top: 142px;
    font-family: "Questrial", sans-serif; font-size: 46px; line-height: 1;
    color: var(--brand-red-deep);
  }
  .address {
    position: absolute; left: 30px; top: 150px;
    font-family: "Arimo", sans-serif; font-size: 13px; letter-spacing: 1px;
    color: var(--ink-soft);
  }
  .contact {
    position: absolute; left: 30px; top: 182px; color: var(--paper);
    font-family: "Arimo", sans-serif;
  }
  .contact-name { font-size: 19px; font-weight: 700; }
  .contact-title { font-size: 13px; font-weight: 400; }
  .contact-lines { list-style: none; margin-top: 8px; padding-left: 12px; font-size: 13px; line-height: 22px; letter-spacing: .5px; }

  /* Back */
  .card-back {
    background: var(--brand-red);
    display: flex; flex-direction: column; align-items: center; justify-content: center;
  }
  .back-mark {
    display: flex; align-items: center; gap: 14px;
    font-family: "Questrial", sans-serif; font-size: 52px; color: var(--paper); line-height: 1;
    margin-top: -30px;
  }
  .back-mark-ring {
    width: 46px; height: 46px; border-radius: 50%; border: 6px solid var(--paper);
  }
  .web {
    position: absolute; bottom: 34px; right: 0; left: 0; text-align: center;
    font-family: "Questrial", sans-serif; font-size: 18px; letter-spacing: 3px;
    color: var(--paper);
  }
</style>
</head>
<body>
<main class="canvas">
  <section class="card card-front" aria-label="Business card front">
    <header class="front-head">
      <div class="wordmark"><span class="wordmark-dot"></span>RB Tolvane</div>
      <p class="tagline">renovating spaces with care</p>
    </header>
    <span class="front-mark" aria-hidden="true">RB</span>
    <p class="address">Door No. Street Name City Name, State, Zip Code.</p>
    <div class="contact">
      <p><span class="contact-name">Your Name,</span> <span class="contact-title">Title</span></p>
      <ul class="contact-lines">
        <li>p: 123-456-7890</li>
        <li>c: 123-456-7890</li>
        <li>e: info@rbtolvane.com</li>
      </ul>
    </div>
  </section>

  <section class="card card-back" aria-label="Business card back">
    <div class="back-mark"><span class="back-mark-ring"></span>RB Tolvane</div>
    <p class="web">www.rbtolvane.com</p>
  </section>
</main>
</body>
</html>
```